I would like a single page website for Skyward Rentals Pacific. In the file list provided there is basic information to be included as well as our logo with colors, fonts and images to be included.
Site must be very simple and be able to be loaded onto smart phones etc very quickly.
Site needs to be very smart in appearance

Target Market(s)

All prospective drone customers from Police to Parties.

Industry/Entity Type

Hire

Requirements
Must have
• Must have variation of color schemes supplied
Nice to have
• Must be very eye catching without going over the top
Should not have
• Anything slow to load.

```html
<!DOCTYPE html>
<html lang="en">
<head>
<meta charset="utf-8">
<title>Skyward Rentals Pacific</title>
<link rel="stylesheet" href="https://fonts.googleapis.com/css2?family=Michroma&family=Open+Sans:wght@400;600&family=Ubuntu:wght@400;500&display=swap">
<style>
:root{
  --navy:#2f3f6b;
  --logo:#3b4a78;
  --text:#4a4a4a;
  --muted:#666;
  --band:#e3e3e3;
  --footer-top:#4a5a88;
  --footer-bottom:#3c4a75;
  --white:#fff;
}
*{margin:0;padding:0;box-sizing:border-box}
html,body{width:1000px;height:1200px;overflow:hidden}
body{position:relative;background:var(--white);font-family:"Open Sans",sans-serif;color:var(--text)}
.abs{position:absolute}
.topline{left:0;top:0;width:1000px;height:2px;background:var(--logo)}
.header-bg{left:0;top:0;width:1000px;height:448px;background:linear-gradient(#fff,#f4f4f4)}
.band{left:0;top:448px;width:1000px;height:614px;background:var(--band)}
.sheet{left:110px;top:98px;width:780px;height:964px;background:var(--white)}
.brand{left:110px;top:30px;display:flex;align-items:center;gap:8px;font-family:"Ubuntu",sans-serif;font-weight:500;font-size:21px;color:var(--logo);letter-spacing:.5px}
.brand-dot{width:14px;height:14px;border-radius:50%;background:var(--logo)}
.call{left:728px;top:27px;font-family:"Ubuntu",sans-serif;font-size:13px;color:#555}
.call-icon{left:866px;top:24px}
.nav{top:67px;font-family:"Ubuntu",sans-serif;font-size:11.5px;color:#333}
.nav.active{color:var(--navy);font-weight:500}
.nav-bar{left:498px;top:95px;width:41px;height:3px;background:var(--navy)}
.hero{left:110px;top:98px;width:780px;height:361px;border-radius:3px 3px 0 0;background:radial-gradient(ellipse at 40% 60%,#e7a873 0%,#b9716b 35%,#6e4d6b 70%,#3c3550 100%)}
.arrow{top:279px}
.cap1{left:146px;top:358px;height:34px;background:rgba(60,55,70,.55);color:#fff;font-family:"Michroma",sans-serif;font-size:11.5px;line-height:18px;padding:8px 22px;white-space:nowrap}
.cap2{left:146px;top:392px;height:32px;background:rgba(60,55,70,.45);color:#fff;font-family:"Ubuntu",sans-serif;font-size:13.5px;line-height:20px;letter-spacing:.4px;padding:6px 22px;white-space:nowrap}
.dots{left:487px;top:467px;display:flex;gap:4px}
.dots span{width:5px;height:5px;border-radius:50%;background:#bbb}
.dots span:first-child{background:var(--navy)}
.welcome{left:110px;top:497px;width:780px;text-align:center;font-family:"Michroma",sans-serif;font-size:17px;color:#333}
.tagline{left:110px;top:524px;width:780px;text-align:center;font-family:"Ubuntu",sans-serif;font-size:15.5px;color:#333}
.product-img{left:120px;top:567px;width:282px;height:193px;border:1px solid #ccc;background:#fff;padding:6px}
.product-img div{width:100%;height:100%;background:radial-gradient(ellipse at center,#e9e9e9 0%,#f8f8f8 55%,#fff 100%)}
.intro{left:425px;top:562px;width:400px;font-family:"Ubuntu",sans-serif;font-size:10px;line-height:14.5px;letter-spacing:.3px;color:#555}
.item{display:flex;gap:7px;font-size:9.5px;line-height:13.5px;color:#555;width:205px}
.tick{flex:none;width:11px;height:11px;border-radius:2px;background:var(--navy);margin-top:1px}
.gallery-title{left:110px;top:803px;width:780px;text-align:center;font-family:"Michroma",sans-serif;font-size:18px;color:#333}
.shot{top:852px;width:181px;height:125px}
.more{left:453px;top:990px;width:87px;height:23px;border:1px solid var(--navy);border-radius:2px;text-align:center;font-family:"Ubuntu",sans-serif;font-size:9.5px;font-weight:500;line-height:21px;color:var(--navy)}
.footer{left:0;top:1062px;width:1000px;height:138px;background:linear-gradient(var(--footer-top),var(--footer-bottom))}
.fnav{top:1094px;font-size:9.5px;color:#fff}
.fnav.pill{left:109px;top:1091px;width:47px;height:21px;border:1px solid #fff;border-radius:11px;text-align:center;line-height:19px}
.social{top:1091px;width:12px;height:12px;border-radius:50%;background:#fff;opacity:.9}
.tooltip{left:817px;top:1114px;width:51px;height:17px;border-radius:9px;background:#9aa0b4;color:#fff;font-size:7px;font-weight:600;text-align:center;line-height:17px;letter-spacing:.3px}
.fline{left:110px;top:1132px;width:790px;height:1px;background:rgba(255,255,255,.15)}
.fitem{top:1152px;display:flex;gap:8px;align-items:flex-start;font-size:8.5px;line-height:12px;color:#dfe3ee}
.ficon{flex:none;width:18px;height:18px;border-radius:50%;background:#fff}
.copy{left:711px;top:1157px;font-size:8.5px;color:#c9cedd}
</style>
</head>
<body>
<div class="abs topline"></div>
<div class="abs header-bg"></div>
<div class="abs band"></div>
<div class="abs sheet"></div>

<header>
  <div class="abs brand"><span class="brand-dot"></span>Skyward Rentals Pacific</div>
  <div class="abs call">Call Us : 0400 555 123</div>
  <svg class="abs call-icon" width="24" height="24" viewBox="0 0 24 24" aria-hidden="true">
    <circle cx="12" cy="12" r="10.5" fill="none" stroke="#3b4a78" stroke-width="1.8"/>
    <path d="M8.5 7.5c.5-.5 1.2-.4 1.5.2l.8 1.6c.2.4.1.8-.2 1.1l-.6.5c.6 1.3 1.6 2.3 2.9 2.9l.5-.6c.3-.3.7-.4 1.1-.2l1.6.8c.6.3.7 1 .2 1.5l-.8.8c-.6.6-1.6.7-2.4.3-2.3-1.1-4.1-2.9-5.2-5.2-.4-.8-.3-1.800.3-2.4z" fill="#3b4a78"/>
  </svg>
  <nav>
    <span class="abs nav active" style="left:503px">Home</span>
    <span class="abs nav" style="left:561px">About Us</span>
    <span class="abs nav" style="left:633px">Services</span>
    <span class="abs nav" style="left:701px">Product</span>
    <span class="abs nav" style="left:768px">Gallery</span>
    <span class="abs nav" style="left:830px">Contact Us</span>
  </nav>
  <div class="abs nav-bar"></div>
</header>

<section>
  <div class="abs hero" role="img" aria-label="Hero photo: white camera drone hovering in front of silhouetted party crowd at sunset"></div>
  <svg class="abs arrow" style="left:127px" width="22" height="22" viewBox="0 0 22 22" aria-hidden="true"><circle cx="11" cy="11" r="11" fill="rgba(40,40,50,.45)"/><path d="M12.5 6.5 8 11l4.5 4.5" fill="none" stroke="#fff" stroke-width="2"/></svg>
  <svg class="abs arrow" style="left:848px" width="22" height="22" viewBox="0 0 22 22" aria-hidden="true"><circle cx="11" cy="11" r="11" fill="rgba(40,40,50,.45)"/><path d="M9.5 6.5 14 11l-4.5 4.5" fill="none" stroke="#fff" stroke-width="2"/></svg>
  <div class="abs cap1">4K Video Footage, 12mp Images</div>
  <div class="abs cap2">We give drones on hire for parties, surveillance, security etc</div>
  <div class="abs dots"><span></span><span></span><span></span></div>
</section>

<section>
  <h1 class="abs welcome" style="font-weight:400">Welcome To Skyward Rentals Pacific</h1>
  <h2 class="abs tagline" style="font-weight:400">4K Video Footage, 12mp Images</h2>
  <div class="abs product-img"><div role="img" aria-label="Product photo: white quadcopter drone with gimbal camera"></div></div>
  <p class="abs intro">ASRA certified company and ASRA endorsed pilot, with Full Public Liability Insurance. All operating licences are in place and are carried on the operator. All drones are maintained to full ASRA compliance standards</p>

  <div class="abs item" style="left:424px;top:621px"><span class="tick"></span>Special Occasions, Children's Birthday Parties, Weddings</div>
  <div class="abs item" style="left:424px;top:655px"><span class="tick"></span>Real Estate Brochures</div>
  <div class="abs item" style="left:424px;top:688px"><span class="tick"></span>Surveillance – Police, Local councils-worksafeetc</div>
  <div class="abs item" style="left:424px;top:721px"><span class="tick"></span>Lost pets</div>
  <div class="abs item" style="left:424px;top:748px"><span class="tick"></span>Insurance assessing</div>
  <div class="abs item" style="left:637px;top:621px"><span class="tick"></span>Sporting events –4K Video of yourself participating in marathons etc</div>
  <div class="abs item" style="left:637px;top:655px"><span class="tick"></span>Construction project updates for remote stake holders</div>
  <div class="abs item" style="left:637px;top:688px"><span class="tick"></span>Building/Roof Condition Inspections</div>
  <div class="abs item" style="left:637px;top:721px"><span class="tick"></span>Accident reconstructions</div>
</section>

<section>
  <h2 class="abs gallery-title" style="font-weight:400">Our Gallery</h2>
  <div class="abs shot" style="left:120px;background:linear-gradient(135deg,#f3e2a8,#8a7a5a 50%,#3f4a2c)" role="img" aria-label="Gallery photo: guests toasting at an outdoor wedding"></div>
  <div class="abs shot" style="left:312px;background:linear-gradient(160deg,#bdbdbd,#6d6d6d 55%,#3a3a3a)" role="img" aria-label="Gallery photo: black and white crowd at a dance hall"></div>
  <div class="abs shot" style="left:505px;background:linear-gradient(150deg,#d9e7b0,#6f8f3e 50%,#2f4a1e)" role="img" aria-label="Gallery photo: friends at a garden table party"></div>
  <div class="abs shot" style="left:698px;background:linear-gradient(140deg,#6a3a3a,#b85a3a 50%,#f0b060)" role="img" aria-label="Gallery photo: child with a birthday cake and candles"></div>
  <div class="abs more">MORE</div>
</section>

<footer>
  <div class="abs footer"></div>
  <div class="abs fnav pill">Home</div>
  <span class="abs fnav" style="left:168px">About Us</span>
  <span class="abs fnav" style="left:230px">Services</span>
  <span class="abs fnav" style="left:288px">Product</span>
  <span class="abs fnav" style="left:344px">Gallery</span>
  <span class="abs fnav" style="left:397px">Contact Us</span>
  <span class="abs social" style="left:813px"></span>
  <span class="abs social" style="left:836px"></span>
  <span class="abs social" style="left:859px"></span>
  <span class="abs social" style="left:882px"></span>
  <div class="abs tooltip">PORTFOLIO</div>
  <div class="abs fline"></div>
  <div class="abs fitem" style="left:110px">
    <svg class="ficon" viewBox="0 0 18 18" aria-hidden="true"><circle cx="9" cy="9" r="9" fill="#fff"/><path d="M9 4.5a3 3 0 0 0-3 3c0 2.2 3 5.8 3 5.8s3-3.6 3-5.8a3 3 0 0 0-3-3z" fill="#3c4a75"/><circle cx="9" cy="7.5" r="1.1" fill="#fff"/></svg>
    <span>14 Harbour Lane, Coral Bay, Northshore<br>4820, Pacific</span>
  </div>
  <div class="abs fitem" style="left:339px">
    <svg class="ficon" viewBox="0 0 18 18" aria-hidden="true"><circle cx="9" cy="9" r="9" fill="#fff"/><path d="M6 5c.4-.4 1-.3 1.2.2l.6 1.2c.2.3.1.7-.2.9l-.4.4c.5 1 1.3 1.8 2.3 2.3l.4-.4c.2-.3.6-.4.9-.2l1.2.6c.5.2.6.8.2 1.2l-.6.6c-.5.5-1.3.6-1.9.3a8 8 0 0 1-4-4c-.3-.6-.2-1.4.3-1.9z" fill="#3c4a75"/></svg>
    <span style="padding-top:3px">0400 555 123</span>
  </div>
  <div class="abs fitem" style="left:440px">
    <svg class="ficon" viewBox="0 0 18 18" aria-hidden="true"><circle cx="9" cy="9" r="9" fill="#fff"/><rect x="5" y="6" width="8" height="6" rx="1" fill="#3c4a75"/><path d="M5.3 6.4 9 9.3l3.7-2.9" fill="none" stroke="#fff" stroke-width=".8"/></svg>
    <span style="padding-top:3px">info@skywardrentals.example</span>
  </div>
  <div class="abs copy">©Copyright 2015 skywardrentals. All Rights Reserved.</div>
</footer>
</body>
</html>
```